Kinderbuchautor sucht emotionales Webdesign
Zielgruppe
Ich bin Autor von Kinderbüchern und suche jemanden,d er meine Website 'Kind- und Elterngerecht' gestalten kann und hier vielleicht gute Ideen oder bestenfalls schon Erfahrung hat.
Ich habe vor ein paar Jahren begonnen, Kinderbücher zu schreiben. Meine Bücher konzentrieren sich auf Kinder zwischen 0 und 12 Jahren. Ich schreibe auf Deutsch und auf Englisch und arbeite mit verschiedenen internationalen Illustratoren zusammen, mit denen ich immer neue Konzepte entwickele.
Formate sind u.a.
- Bilderbücher in verschiedenen Sprachen (insbes. Deutsch und Englisch, aber auch Spanisch, französisch und z.T. Chinesisch)
- Bilinguale Bilderbücher und Erstlese-Bücher (diese sind in der Tat zweisprachig)
- Romane für 8-12 jährige
- einsprachige Erstlese-Bücher
- Chapter Books (zwischen 60 und 100 Seiten)
Mit meinen Geschichten bin ich in erster Linie daran interessiert, neue Erfahrungen zu vermitteln und Anregungen für neue Perspektiven auf die Welt zu geben. Ich möchte das auf spielerische Weise tun, allerdings nicht zufällig. Das Schreiben aus der Perspektive der Kinder öffnet die Tür zu Welten, die von Elfen und Tieren, Meerjungfrauen und Königen, Zwergen und Riesen bevölkert sind – Wesen, die Probleme haben und sie lösen können, indem sie einfach die Beschränkungen unserer realen Welt umgehen. Das Mögliche zu entdecken, wo nichts wahrscheinlich erscheint.
Die Zielgruppe sind in erster Linie Eltern, Großeltern, Lehrer, Pädagogen etc.
Aufgabenstellung
Es geht bei dieser Website insbesondere darum, die richtige Emotion rüber zu bringen. Da viele Bücher zweisprachig sind oder die Bücher in verschiedenen Sprachen veröffentlicht werden, kann auch der Lerncharakter herausgestellt werden. Ich will allerdings nicht, dass die Website mit Lernhilfen für Pädagogen gespickt ist das ist nicht das Ziel. Das ganze soll den Fun-Faktor unterstreichen. Zum Beispiel gibt es in den USA fast eine große Anzahl von sog. 'Home-Learning' Initiativen, bei denen Kinder schon sehr früh mit. z.B. Hilfe von Bilderbüchern und leichten Erstlesebüchern andere Sprachen lernen, das ganze aber nicht als Lernprogramm sehen. Das ist einfach so, weil die Eltern aus zwei verschiedenen Kulturkreisen kommen. Das ist noch weitgehend eine Nische.
Aus diesem Grund werden die Bücher auch im internationalen Bereich, z.B. USA, Kanada, Spanien, Australien und UK vermarktet, neben D-A-CH.
Es gibt bereits eine Website, die aber NICHT als Vorlage genommen werden soll. Hier kann sich an den FARBEN orientiert werden: www.haraldwenke.com.
DIe Website wurde mit ZUPO erstellt. ZUPO ist aber keine zwingende Vorgabe. Es geht darum, die richtige Emotion zu kreieren.
Beipiele von Seiten, die mir hier gut gefallen, weil sie auch Social-Media optimiert sind, sind z.B. die folgenden:
http://dorvane.com/
https://www.melvinharrowgate.com/
http://www.lucasferndale.com/
Ich habe ein Logo, das ist ein Name 'Harald Wenke' mit der Schrift Luna Bar. Ich habe Illustrationen und Fotos sowie Cover der Bücher als Attachment beigefügt.

```html
<!DOCTYPE html>
<html lang="de">
<head>
<meta charset="utf-8">
<title>Harald Wenke – Startseite mobil</title>
<link rel="stylesheet" href="https://fonts.googleapis.com/css2?family=Reenie+Beanie&family=Roboto+Condensed:wght@300;400&display=swap">
<style>
  :root {
    --stage: #ececec;
    --paper: #ffffff;
    --ink: #1a1a1a;
    --accent-red: #e0231c;
    --rule: #dcdcdc;
    --muted: #333333;
    --menu: #9a9a9a;
  }
  html, body {
    margin: 0;
    width: 1200px;
    height: 801px;
    overflow: hidden;
    background: var(--stage);
  }
  .stage {
    width: 1200px;
    height: 801px;
    display: flex;
    align-items: center;
    justify-content: center;
  }
  .mobile-page {
    width: 420px;
    height: 747px;
    background: var(--paper);
    display: flex;
    flex-direction: column;
    overflow: hidden;
    box-shadow: 0 2px 12px rgba(0,0,0,0.08);
  }
  .site-header {
    height: 64px;
    flex: 0 0 64px;
    display: flex;
    align-items: center;
    justify-content: space-between;
    padding: 0 20px;
    border-bottom: 1px solid var(--rule);
  }
  .brand-name {
    font-family: "Roboto Condensed", sans-serif;
    font-weight: 400;
    font-size: 20px;
    color: var(--ink);
  }
  .menu-toggle { display: block; }
  .welcome {
    text-align: center;
    padding: 22px 30px 0;
  }
  .welcome-title {
    font-family: "Reenie Beanie", cursive;
    font-weight: 400;
    font-size: 104px;
    line-height: 0.9;
    margin: 0;
    color: var(--ink);
  }
  .welcome-subtitle {
    font-family: "Reenie Beanie", cursive;
    font-size: 40px;
    line-height: 1;
    margin: 6px 0 14px;
    color: var(--accent-red);
  }
  .welcome-text {
    font-family: "Roboto Condensed", sans-serif;
    font-weight: 300;
    font-size: 14px;
    line-height: 1.4;
    color: var(--muted);
    margin: 0 auto;
    max-width: 320px;
  }
  .author-visual {
    flex: 1;
    margin: 18px 36px 0;
    background:
      radial-gradient(ellipse 60% 40% at 50% 38%, rgba(214,164,120,0.9) 0%, rgba(214,164,120,0) 100%),
      linear-gradient(180deg, #fbfaf7 0%, #eadfcf 22%, #b98558 46%, #d8262b 68%, #242424 88%);
  }
</style>
</head>
<body>
<main class="stage">
  <section class="mobile-page">
    <header class="site-header">
      <span class="brand-name">Harald Wenke</span>
      <svg class="menu-toggle" width="26" height="20" viewBox="0 0 26 20" aria-label="Menü">
        <rect y="1" width="26" height="3" fill="var(--menu)"/>
        <rect y="8.5" width="26" height="3" fill="var(--menu)"/>
        <rect y="16" width="26" height="3" fill="var(--menu)"/>
      </svg>
    </header>
    <div class="welcome">
      <h1 class="welcome-title">Hallo!</h1>
      <p class="welcome-subtitle">Willkommen auf meiner<br>Website…</p>
      <p class="welcome-text">Danke für Deine Zeit. Du bist dabei, mehr über meine Bücher und mich selbst zu erfahren. Finde heraus, was es Neues bei mir gibt. Viel Spaß!</p>
    </div>
    <div class="author-visual" role="img" aria-label="Foto des Autors mit Schiebermütze und roter Clownsnase, umgeben von gezeichnetem Fuchs und Dachs"></div>
  </section>
</main>
</body>
</html>
```